Executive Performance Review mapped on J-curve

I need to turn an executive company performance review into a visual infographic. The list of accomplishments is grouped into four calendar quarters. Each quarter needs a subtle representation of the season. The four quarters and associated list of accomplishments need to be mapped to a J-curve. - Spreadsheet with accomplishments attached (Marlowbend)- Sample image of a J-curve. You can google J-curve to see more images.- The title should be "Danica Ostrander Year in Review"

Target Market(s)

Board of Directors

Requirements
Nice to have
• This will be presented to a company founder that is an artist and customer experience expert. He is very visual so a nice visual representation of the data will be impactful. He also uses the phrase that you have to live with or work with someone for four seasons before you really know them. This is why I have the seasons mapped to the quarters. The Fall season motif should be gloomy and stormy.

```html
<!DOCTYPE html>
<html lang="en">
<head>
<meta charset="utf-8">
<title>Danica Ostrander – Year One in Review</title>
<link href="https://fonts.googleapis.com/css2?family=Source+Sans+3:wght@400;600;700;800&display=swap" rel="stylesheet">
<style>
:root{
  --ink:#1f1f1f;
  --muted:#444;
  --summer:#fcd116;--summer-pill:#fde98a;--summer-bg:#fefbe8;
  --fall:#4d5b66;--fall-pill:#9fb0b8;--fall-bg:#dde8eb;
  --winter:#a6dbe8;--winter-pill:#d3eef5;--winter-bg:#f2f9fc;
  --spring:#c4df4c;--spring-pill:#e3f0a6;--spring-bg:#f4f9e2;
  --green:#2f7f33;--green-pill:#6ba46c;
  --curve:#b4b4b4;
}
*{box-sizing:border-box;margin:0;padding:0}
html,body{width:1200px;height:693px;overflow:hidden;background:#fff}
body{font-family:"Source Sans 3",Arial,sans-serif;color:var(--ink)}
.canvas{width:1200px;height:693px;overflow:hidden;position:relative}
.stage{position:absolute;left:0;top:0;width:1500px;height:866px;transform:scale(.8);transform-origin:0 0}
.backdrop{position:absolute;left:0;top:0}
.header{position:absolute;left:64px;top:83px}
.header h1{font-size:16px;font-weight:800;letter-spacing:-.2px;line-height:19px}
.header .date{font-size:15px;font-weight:400;line-height:17px}
.header .company{font-size:11px;color:var(--muted);margin-top:1px}
.season-bar{position:absolute;top:138px;height:20px;color:#fff;font-weight:700;font-size:14px;text-align:center;line-height:20px}
.quarter-pill{position:absolute;top:158px;height:20px;width:122px;border-radius:0 0 8px 8px;font-size:11.5px;font-weight:700;text-align:center;line-height:20px}
.column{position:absolute;font-size:11px;line-height:12px}
.group{position:relative;padding-left:36px;margin-bottom:16px}
.group .icon{position:absolute;left:4px;top:0;width:24px;height:24px}
.group h3{font-size:11.5px;font-weight:700;line-height:14px;margin-bottom:3px}
.group ul{list-style:none}
.group li{padding-left:8px;position:relative;margin-bottom:4.4px}
.group li::before{content:"•";position:absolute;left:0}
.group.tight li{margin-bottom:2px;padding-left:6px}
.greenfield-list{position:absolute;left:1195px;top:436px;color:#fff}
.greenfield-list h3{font-size:12px;font-weight:700;margin-bottom:3px}
.greenfield-list li{list-style:none;font-size:13.5px;line-height:15px;margin-bottom:3.5px}
.stage-label{position:absolute;top:777px;font-size:11.5px;font-weight:700;text-align:center}
.coin{position:absolute;border-radius:50%;text-align:center;font-size:9.5px;font-weight:700;color:#fff;display:flex;flex-direction:column;align-items:center;justify-content:center;line-height:1.3}
.coin svg{width:16px;height:16px;margin-bottom:2px}
</style>
</head>
<body>
<div class="canvas">
<div class="stage">

<svg class="backdrop" width="1500" height="866" viewBox="0 0 1500 866">
  <defs>
    <clipPath id="under-curve">
      <path d="M63,625 C250,690 420,725 610,680 C760,650 900,600 1030,522 C1180,430 1300,310 1425,168 L1432,168 L1432,795 L63,795 Z"/>
    </clipPath>
    <linearGradient id="summer-ground" x1="0" y1="0" x2="0" y2="1"><stop offset="0" stop-color="#fbe26a"/><stop offset="1" stop-color="#f4c40e"/></linearGradient>
    <linearGradient id="fall-ground" x1="0" y1="0" x2="0" y2="1"><stop offset="0" stop-color="#8a949c"/><stop offset="1" stop-color="#3d4953"/></linearGradient>
    <linearGradient id="winter-ground" x1="0" y1="0" x2="0" y2="1"><stop offset="0" stop-color="#d6f0f7"/><stop offset="1" stop-color="#ffffff"/></linearGradient>
    <linearGradient id="spring-ground" x1="0" y1="0" x2="1" y2="1"><stop offset="0" stop-color="#dbeeb0"/><stop offset="1" stop-color="#8ccb3a"/></linearGradient>
    <linearGradient id="green-ground" x1="0" y1="0" x2="1" y2="0"><stop offset="0" stop-color="#5fb54a"/><stop offset="1" stop-color="#2a7a2e"/></linearGradient>
    <linearGradient id="green-sky" x1="0" y1="0" x2="1" y2="1"><stop offset="0" stop-color="#e2efdd"/><stop offset="1" stop-color="#b9d7b4"/></linearGradient>
  </defs>
  <rect x="63" y="158" width="273" height="637" fill="var(--summer-bg)"/>
  <rect x="336" y="158" width="275" height="637" fill="var(--fall-bg)"/>
  <rect x="611" y="158" width="276" height="637" fill="var(--winter-bg)"/>
  <rect x="887" y="158" width="276" height="637" fill="var(--spring-bg)"/>
  <rect x="1163" y="158" width="269" height="637" fill="url(#green-sky)"/>
  <g clip-path="url(#under-curve)">
    <g role="img" aria-label="Summer beach scene with sun, palm trees and a deck chair">
      <rect x="63" y="560" width="273" height="235" fill="url(#summer-ground)"/>
    </g>
    <g role="img" aria-label="Gloomy fall storm with rain clouds and falling leaves">
      <rect x="336" y="560" width="275" height="235" fill="url(#fall-ground)"/>
    </g>
    <g role="img" aria-label="Winter snowfall scene with a snowman">
      <rect x="611" y="560" width="276" height="235" fill="url(#winter-ground)"/>
    </g>
    <g role="img" aria-label="Spring meadow with daisies, butterflies and a bird">
      <rect x="887" y="400" width="276" height="395" fill="url(#spring-ground)"/>
    </g>
    <g role="img" aria-label="Greenfield rising hill of lush green growth">
      <rect x="1163" y="150" width="269" height="645" fill="url(#green-ground)"/>
    </g>
  </g>
  <g stroke="#cfcfcf" stroke-width="1" stroke-dasharray="4 3">
    <line x1="336" y1="178" x2="336" y2="795"/><line x1="611" y1="178" x2="611" y2="795"/><line x1="887" y1="178" x2="887" y2="795"/><line x1="1163" y1="178" x2="1163" y2="795"/>
  </g>
  <path d="M63,625 C250,690 420,725 610,680 C760,650 900,600 1030,522 C1180,430 1300,310 1418,176" fill="none" stroke="var(--curve)" stroke-width="5"/>
  <path d="M1432,158 L1404,172 L1424,190 Z" fill="var(--curve)"/>
  <circle cx="188" cy="662" r="36" fill="#fff3a8" opacity=".6"/>
  <circle cx="470" cy="703" r="36" fill="#7c8790" opacity=".6"/>
  <circle cx="746" cy="653" r="36" fill="#dff2f8" opacity=".7"/>
  <circle cx="1030" cy="522" r="36" fill="#eef6b8" opacity=".7"/>
  <circle cx="1300" cy="302" r="40" fill="#7cb47b" opacity=".6"/>
</svg>

<header class="header">
  <h1>DANICA OSTRANDER - YEAR ONE IN REVIEW</h1>
  <div class="date">JULY 1, 2019</div>
  <div class="company">KESTREL FORGE, INC.</div>
</header>

<div class="season-bar" style="left:63px;width:273px;background:var(--summer)">SUMMER</div>
<div class="season-bar" style="left:336px;width:275px;background:var(--fall)">FALL</div>
<div class="season-bar" style="left:611px;width:276px;background:var(--winter)">WINTER</div>
<div class="season-bar" style="left:887px;width:276px;background:var(--spring)">SPRING</div>
<div class="season-bar" style="left:1163px;width:269px;background:var(--green)">GREENFIELD</div>
<div class="quarter-pill" style="left:138px;background:var(--summer-pill)">Q3 2018</div>
<div class="quarter-pill" style="left:412px;background:var(--fall-pill)">Q4 2018</div>
<div class="quarter-pill" style="left:686px;background:var(--winter-pill)">Q1 2019</div>
<div class="quarter-pill" style="left:964px;background:var(--spring-pill)">Q2 2019</div>
<div class="quarter-pill" style="left:1236px;background:var(--green-pill);color:#fff">2020</div>

<svg width="0" height="0" style="position:absolute">
  <symbol id="i-transition" viewBox="0 0 24 24"><path d="M14 3h7v7M21 3l-9 9M11 5H4v15h15v-7" fill="none" stroke="#333" stroke-width="1.6"/></symbol>
  <symbol id="i-org" viewBox="0 0 24 24"><g fill="none" stroke="#333" stroke-width="1.4"><circle cx="5" cy="12" r="3"/><rect x="15" y="2" width="6" height="5"/><rect x="15" y="10" width="6" height="5"/><rect x="15" y="18" width="6" height="5"/><path d="M8 12h4M12 4v16M12 4h3M12 12h3M12 20h3"/></g></symbol>
  <symbol id="i-strategy" viewBox="0 0 24 24"><g fill="none" stroke="#333" stroke-width="1.4"><path d="M2 3l4 4M6 3l-4 4M2 17l4 4M6 17l-4 4"/><circle cx="20" cy="5" r="2.5"/><path d="M5 19c6 0 3-12 12-13"/></g></symbol>
  <symbol id="i-tag" viewBox="0 0 24 24"><g fill="none" stroke="#333" stroke-width="1.4"><path d="M3 9l7-7 11 11-7 7z"/><circle cx="8" cy="7" r="1.3"/><path d="M12 10v6M10 12h4"/></g></symbol>
  <symbol id="i-hire" viewBox="0 0 24 24"><g fill="none" stroke="#333" stroke-width="1.4"><circle cx="10" cy="10" r="7"/><circle cx="10" cy="8" r="2.2"/><path d="M6 14c1-2 7-2 8 0M15 15l6 6"/></g></symbol>
  <symbol id="i-coin" viewBox="0 0 24 24"><g fill="none" stroke="#fff" stroke-width="1.6"><path d="M9 3h6l-2 4h-2z"/><path d="M11 7C5 10 4 21 12 21s7-11 1-14"/><path d="M12 11v7M10 13h3a1.2 1.2 0 010 2.4h-2a1.2 1.2 0 000 2.4h3"/></g></symbol>
</svg>

<div class="column" style="left:66px;top:188px;width:268px">
  <div class="group tight"><svg class="icon"><use href="#i-transition"/></svg><h3>TRANSITIONS</h3><ul>
    <li>RO Transition from Ravi &amp; Lena</li><li>Start CR Office Initiative</li><li>Tactical Ops transition from Ravi</li><li>Formalize Exec Team</li></ul></div>
  <div class="group"><svg class="icon"><use href="#i-org"/></svg><h3>BIZ ARCHITECTURE</h3><ul>
    <li>Independent Financial Audit</li><li>Organizational Audit - Structure</li><li>Organizational Audit - People</li><li>XF Framework - ESU</li><li>Defined Utilization, Realization, Availability</li></ul></div>
  <div class="group"><svg class="icon"><use href="#i-strategy"/></svg><h3>STRATEGY</h3><ul>
    <li>Effective Strategy Meeting</li><li>Strategic Themes 2018 - 2020: Stablize,<br>Accelerate, Surge</li><li>Business Drivers: Drive Revenue, Improve</li><li>Kestrelite Experience, Increase Brand Awareness</li></ul></div>
  <div class="group"><svg class="icon"><use href="#i-tag"/></svg><h3>SALES</h3><ul>
    <li>Tallowmere Account Transition</li><li>Brinda Account Transition</li><li>2 year Managed Services Engagement<br>Model</li></ul></div>
</div>

<div class="column" style="left:340px;top:186px;width:268px">
  <div class="group"><svg class="icon"><use href="#i-org"/></svg><h3>BIZ ARCHITECTURE</h3><ul>
    <li>XF Framework - Functional Meetings &amp;<br>Scrum of Scrums</li><li>Structured Reorg</li><li>Implemented Reorg</li><li>Quarterly Org Iteration cadence</li><li>Defined Key Hire Plan</li><li>CR Office Operational</li><li>Time Accountability</li><li>Tools ReConfig</li><li>Org Structure v1</li></ul></div>
  <div class="group"><svg class="icon"><use href="#i-strategy"/></svg><h3>STRATEGY</h3><ul><li>Internal QBR Accountability</li></ul></div>
  <div class="group"><svg class="icon"><use href="#i-tag"/></svg><h3>SALES</h3><ul><li>Corvane QBR</li><li>Tallowmere QBR</li></ul></div>
</div>

<div class="column" style="left:615px;top:188px;width:268px">
  <div class="group"><svg class="icon"><use href="#i-org"/></svg><h3>BIZ ARCHITECTURE</h3><ul>
    <li>XF Framework - Progress Demos</li><li>Org Structure - COE's</li><li>Stablize Accounting &amp; Finance</li><li>Exec Hiring Process</li></ul></div>
  <div class="group"><svg class="icon"><use href="#i-hire"/></svg><h3>KEY HIRES</h3><ul><li>Controller</li><li>Director CX</li></ul></div>
  <div class="group"><svg class="icon"><use href="#i-strategy"/></svg><h3>STRATEGY</h3><ul>
    <li>Founders removed from front line activity</li><li>Kestrel QBR - Goal Setting &amp; Tracking</li></ul></div>
  <div class="group"><svg class="icon"><use href="#i-tag"/></svg><h3>SALES</h3><ul><li>Brinda QBR</li><li>Tallowmere QBR</li></ul></div>
</div>

<div class="column" style="left:891px;top:187px;width:268px">
  <div class="group"><svg class="icon"><use href="#i-org"/></svg><h3>BIZ ARCHITECTURE</h3><ul>
    <li>XF Framework - Ideation Process &amp;<br>Sales Cadence</li><li>Consulting Levels &amp; Salary Bands</li><li>Roles &amp; Responsibilities</li></ul></div>
  <div class="group"><svg class="icon"><use href="#i-hire"/></svg><h3>KEY HIRES</h3><ul>
    <li>Interim HR</li><li>Provisional Client Partner</li><li>Acting Director 1</li><li>Acting Director 2</li><li>Client Partner 1</li><li>Sales Exec 1</li></ul></div>
  <div class="group"><svg class="icon"><use href="#i-tag"/></svg><h3>SALES</h3><ul>
    <li>Tiered Pricing Managed Services</li><li>Opened Glasswing Door</li><li>Flipped focus from operationaly run<br>company to sales/marketing<br>driven org</li><li>Pellmark Direct</li></ul></div>
</div>

<div class="greenfield-list">
  <h3>GREENFIELD</h3>
  <ul><li>• Set 2020 Goals</li><li>• Schedule QBRs 1 year out</li><li>• Financial Projections</li><li>• Fully Functional Leadership Team</li><li>• Robust Sales Team</li></ul>
</div>

<div class="coin" style="left:162px;top:636px;width:52px;height:52px;background:#f5c91c"><svg><use href="#i-coin"/></svg>$3.8M<br>1.44%</div>
<div class="coin" style="left:442px;top:675px;width:56px;height:56px;background:#3f4a54;box-shadow:0 0 0 4px #68747d"><svg><use href="#i-coin"/></svg>$4.4M<br>0.58%</div>
<div class="coin" style="left:719px;top:626px;width:54px;height:54px;background:#a3d8e6"><svg><use href="#i-coin"/></svg>$4.8M<br>12.84%</div>
<div class="coin" style="left:1003px;top:495px;width:54px;height:54px;background:#c3df4e"><svg><use href="#i-coin"/></svg>$4.7M<br>8.24%</div>
<div class="coin" style="left:1270px;top:272px;width:60px;height:60px;background:var(--green);box-shadow:0 0 0 4px #5d9c5f"><svg><use href="#i-coin"/></svg>$35M<br>15%</div>

<div class="stage-label" style="left:63px;width:250px">STORMING</div>
<div class="stage-label" style="left:336px;width:275px;color:#fff">ACTIVITY</div>
<div class="stage-label" style="left:611px;width:276px">MARLOWBEND</div>
<div class="stage-label" style="left:887px;width:276px">OUTCOMES</div>
<div class="stage-label" style="left:1163px;width:272px;color:#fff">VALUE CREATION</div>

</div>
</div>
</body>
</html>
```